Digital Imaging Website Design Project

This project is for 3 page designs - The main Home page design, department page design & content page design which will utilize most of the home page components.

Client Background - http://www.klmvxco.example

An almost Forty year old established printing company that has a large client base of architect/engineering, as the print shop opened up as a blueprinting company, and over the years has grown, changed and expanded to offer document and digital file management for this industry. KLMVxco. has also always offered color printing services, but recently has expanded their color department to be able to offer amazing dimensional printing, and extreme cutting technology.

These new products and services will be targeted to new industries for repeatable printing needs, promotional, point of purchase color printing, as well as in-store, interior decor/wall. These new printing services are only offered by KLMVXCO in their area, and they want to convey that they are on the leading edge of color printing technology, while at the same time, not eliminating their existing primary business scaring away their traditional client base of architectural/engineering firms that use them for large format printing, scanning and document management services.

1 - Home Page Design
Primary Goals of the design:

1.Provide a new, eye catching engaging website that conveys the above expansion/growth/cutting edge company.
2.Full screen design please to move away from the 'center' bordered up website they currently have.
3.Design Components – We don't have any media to provide you with exception of our logo. We're looking for fresh design that is exciting and engaging imagery. Additionally, we are working on a color/effected version of our logo to place on the color division page, and this will probably tie in with the design you create for us.
4.It should be designed to be able to work as a responsive design as well so that when installed, will work across devices etc..
5.Colors – Same color scheme, but if you have an accent color you'd like to use to make the site pop, go for it!

Requirements:
1.The 4 divisions of the company should be the main feature so that the client depending on which department they are needing, will see those 4 choices clearly in the design, and they'll know to click on one of them to get more information and to their needed services.

2.The main goal of the site is to get visitors to place an order, there should be a feature on the home page for this call to action.

3.Put in an element that communicates the main benefit of KLMVxco. - an area for a 1-line Statement/Call to Action / Overall Company Benefit/

4.The 4 divisions need to have eye catching elements related to their products and services, and that clearly illustrate that the user should click on that to go to the appropriate area for products and services

Reprographics
This department is specifically geared to architect/engineering industry
BYLine for optional Use: Partnering with Building Industry Providers since 1975
Related pages for better understanding:
http://www.klmvxco.example/services/portland_professional_printing_services
http://www.klmvxco.example/services/reprographics
Digital File Management
This department is related to Architect/engineers, but can also apply to any other industry needing electronic document management, scanning, or archival services.
BYLine for optional use: Effective & Efficient Digital Solutions at every level.
Related Pages:
http://www.klmvxco.example/colorgraphics/electronic_file_document_management
http://www.klmvxco.example/colorgraphics/document_scanning_service
http://www.klmvxco.example/services/scanning_and_archiving

Color Graphics
This Department is newly expanded / has expanded services / they are focusing more of their efforts on this department and is a key reason for updated website design.
This Department image/representation should be stellar in the imagery to convey the excellence of the color department the services availble.
One of their newest products/services is dimensional printing – not 3-D, but raised element printing. Essentially a client could pick components on their graphic that that they want to 'bump' out, and additional layers would be put in place to create a popped out, dimensional effect. * Bonus points for creating the color department image that effectively conveys this new service – whether it's showing an abstract image/element that is actually raised off the page/paper/component. Additionally the color dimensional printing can be done on practically any material – glass, vinyl, material etc.... Please let me know if you have any questions on this.
BYLine for optional Use: See How Our Color Stands Out From the Rest
Related pages:
http://www.klmvxco.example/colorgraphics
http://www.klmvxco.example/colorgraphics/color_digital_imaging

Equipment & Supplies
This department provides specific supplies and hardware vs. printing products/services. Our largest client base is architects/engineers, but is not limited to this industry. Typical equipment is large printers, and supplies are typically paper products geared to the large format printing services, for the architect/engineers industry.
Byline for optional Use: In-House Printing & Fulfillment Services
Related pages:
http://www.klmvxco.example/tarvo_ulix_equipment_sales
http://www.klmvxco.example/supplies

Additionally - Possibly have descriptive text sections below these 4 elements, but this is optional.

2.) Department/Division Page design -

This page should pull the home page element to over based on which division is selected.
Have a submenu design incorporated so that users can navigate to all the products and services that will be listed under that division
Contain a plugin design for FAQs – so that depending on which division page they are on, the appropriate FAQ's would display for use to have easy access to.
Contain a plugin design for – Contact Us easy form – short form –
Name
Company
Number
Email
Project Details/Questions: Text box

3.)Content Page design
This page should have main area for content
Area for an image with slideshow of other supporting images
Optional area for video – most (99%) of the pages will not have videos, but in the case we do, would like an area that will display videos effectively.
Optional FAQ plugin display
Contact plugin display

Global Elements:

Static and very visible site features that are in a position so that if user clicks beyond home page will still see these are:
Get a Quote
Place Order
Digital Plan-room
Call Today - 555-384-7290

Other global components:
SM Icons – QN, Chirpa, Workrung
Rotating Testimonial

Navigational Menu:
The KLM Difference
About
Sustainability
Products & Services
Reprograhics
Digital File Management
Color Graphics
Equipment & Supplies
Login
Blog
Contact Us

After the contest – What would be great to have is when a user clicks on one of the departments, it takes that visual element and continues onto it's department page for a smaller but related image - But this may be an after this web design contest.

Additionally will need some other design work on the interior pages, as well, so hoping to find a great designer to complete the other tasks – as well as be the go-to for future endeavors!

Thanks for looking at the project, and I look forward to any questions you may have.
Updates

Looking forward to hearing from interested designers! - If you're curious about my work, you can find my profile at:  https://www.jobrilly.example/users/~07f3b92e61cd5a0b48

Target Market(s)

Please see description

Industry/Entity Type

Electronic

Requirements
Must have
• Please see description

```html
<!DOCTYPE html>
<html lang="en">
<head>
<meta charset="utf-8">
<title>KLMVxco – Digital Imaging</title>
<link href="https://fonts.googleapis.com/css2?family=Open+Sans:wght@300;400;600;700&display=swap" rel="stylesheet">
<style>
:root{
  --navy:#2b2f7a;
  --navy-dark:#1d2150;
  --red:#e2262c;
  --red-dark:#b8161b;
  --text:#777;
  --text-light:#999;
  --line:#e2e2e2;
  --footer:#2c2c2c;
  --footer-base:#1f1f1f;
}
*{margin:0;padding:0;box-sizing:border-box}
html,body{width:938px;height:1200px;overflow:hidden;background:#fff}
body{position:relative;font-family:'Open Sans',Arial,sans-serif;color:var(--text)}
.abs{position:absolute}
.top-rule{left:0;top:0;width:938px;height:3px;background:var(--navy)}
.util-nav{left:684px;top:4px;width:175px;height:23px;border:1px solid var(--line);border-top:none;display:flex;justify-content:space-around;align-items:center;font-size:9px;color:#555}
.util-nav span::before{content:"";display:inline-block;width:5px;height:5px;background:var(--red);border-radius:1px;margin-right:3px;vertical-align:middle}
.brand{left:78px;top:36px;display:flex;align-items:center;gap:8px}
.brand-mark{width:36px;height:36px;border-radius:50%;background:var(--navy)}
.brand-name{font-size:26px;font-weight:700;color:var(--navy);letter-spacing:-.5px}
.order-bar{left:576px;top:52px;width:283px;height:31px;border-radius:16px;background:linear-gradient(#ef3a3f,var(--red-dark));color:#fff;display:flex;align-items:center;box-shadow:0 1px 2px rgba(0,0,0,.3)}
.order-bar .place{display:flex;align-items:center;gap:8px;padding:0 11px 0 14px;font-weight:700;font-size:14px;border-right:1px solid rgba(255,255,255,.35);height:100%}
.order-bar .call{padding-left:11px;font-size:12px}
.order-bar .call b{font-weight:700;font-size:14px}
.nav-rule{left:0;top:108px;width:938px;height:1px;background:var(--line)}
.main-nav{left:78px;top:108px;height:38px;display:flex;gap:18px;font-size:10.4px;color:#8a8a8a}
.main-nav span{line-height:40px;position:relative}
.main-nav .active{color:var(--red)}
.main-nav .active::before{content:"";position:absolute;left:0;right:0;top:0;height:3px;background:var(--red)}
.hero{left:0;top:146px;width:938px;height:286px;background:linear-gradient(110deg,#273358 0%,#5a6a92 28%,#c9b23c 52%,#d8485c 68%,#e4d34a 82%,#5fb7d6 100%)}
.hero-band{left:0;top:360px;width:938px;height:72px;background:rgba(18,20,48,.88);display:flex;align-items:center;padding-left:78px}
.hero-title{font-size:20.5px;font-weight:600;color:#fff;letter-spacing:-.3px;width:428px}
.hero-copy{font-size:8.6px;line-height:13px;color:#d8d8e6;width:260px}
.btn-red{background:linear-gradient(#ef3a3f,var(--red-dark));color:#fff;font-weight:700;border-radius:12px;text-align:center}
.hero-btn{left:774px;top:385px;width:85px;height:23px;line-height:23px;font-size:10px}
.rule{left:0;width:938px;height:1px;background:var(--line)}
.division{top:476px;width:178px}
.division-head{display:flex;gap:8px;align-items:flex-start}
.division-head svg{flex:none;margin-top:2px}
.division h2{font-size:14.4px;font-weight:400;color:var(--navy);line-height:17px}
.division p{font-size:8.7px;line-height:12.4px;color:var(--text-light);margin-top:12px;letter-spacing:-.1px}
.pill{display:inline-block;margin-top:5px;background:var(--navy);color:#fff;font-size:9.5px;padding:0 8px;border-radius:8px;line-height:14px}
.section-title{display:flex;align-items:center;gap:9px;font-size:15.5px;color:var(--navy)}
.photo{border-radius:1px}
.news-item{left:672px;width:190px;display:flex;gap:8px}
.news-thumb{width:47px;height:48px;flex:none}
.news-item .date{font-size:9.3px;color:#444}
.news-item p{font-size:8.8px;line-height:13.3px;color:var(--text-light)}
.link-red{color:var(--red);font-style:italic;font-size:8.8px;text-decoration:underline}
.testimonial{left:672px;top:898px;width:190px;font-size:8.8px;line-height:15.6px;color:var(--text-light)}
.testimonial .author{color:var(--red);font-style:italic;margin-top:4px}
.dots{left:674px;top:1003px;display:flex;gap:2px}
.dots i{width:6px;height:6px;border-radius:50%;background:#c5c8e0}
.dots i:first-child{background:var(--navy)}
.footer{left:0;top:1026px;width:938px;height:148px;background:var(--footer)}
.footer-base{left:0;top:1174px;width:938px;height:26px;background:var(--footer-base);text-align:center;font-size:8.6px;line-height:26px;color:#8a8a8a}
.footer-col{top:1041px}
.footer-col h3{font-size:11.2px;font-weight:600;color:#fff;margin-bottom:5px}
.footer-col li{list-style:none;font-size:9.1px;line-height:15.7px;color:#9a9a9a}
.social{display:flex;gap:12px;margin-top:8px;font-size:11px;font-weight:700;color:var(--red)}
.news-input{width:191px;height:21px;background:#1b1b1b;border:1px solid #3a3a3a;margin-top:4px}
.submit{display:inline-block;margin-top:8px;width:42px;height:14px;line-height:14px;font-size:7.5px;border-radius:7px;margin-left:1px}
</style>
</head>
<body>
<div class="abs top-rule"></div>
<div class="abs util-nav"><span>Login</span><span>Blog</span><span>Contact Us</span></div>

<div class="abs brand"><div class="brand-mark"></div><div class="brand-name">KLMVxco</div></div>

<div class="abs order-bar">
  <div class="place">
    <svg width="14" height="14" viewBox="0 0 14 14"><rect x="1" y="2" width="10" height="11" fill="none" stroke="#fff" stroke-width="1.5"/><path d="M5 9 L12 2" stroke="#fff" stroke-width="2"/></svg>
    PLACE ORDER
  </div>
  <div class="call">Call : <b>555-384-7290</b></div>
</div>

<div class="abs nav-rule"></div>
<nav class="abs main-nav">
  <span class="active">The KLM Difference</span><span>About</span><span>Sustainability</span><span>Products &amp; Services</span><span>Reprographics</span><span>Digital File Management</span><span>Color Graphics</span><span>Equipment &amp; Supplies</span>
</nav>

<div class="abs hero" role="img" aria-label="Hands holding a colour swatch fan over printed colour calendar sheets"></div>
<div class="abs hero-band">
  <div class="hero-title">Services for Architects, Engineers &amp; Builders</div>
  <div class="hero-copy">Le Lorem Ipsum est simplement du faux texte employé dans la composition et la mise en page avant impression.</div>
</div>
<div class="abs btn-red hero-btn">READ MORE</div>

<div class="abs rule" style="top:456px"></div>

<div class="abs division" style="left:78px">
  <div class="division-head"><svg width="24" height="24" viewBox="0 0 24 24"><circle cx="12" cy="12" r="9" fill="none" stroke="#e2262c" stroke-width="3"/><circle cx="12" cy="12" r="4" fill="#e2262c"/></svg><h2>Reprographics<br>Company</h2></div>
  <p>Si vous voulez utiliser un passage du Lorem Ipsum, vous devez être sûr qu'il n'y a rien d'embarrassant caché dans le texte. Tous les générateurs</p>
  <span class="pill">More</span>
</div>
<div class="abs division" style="left:282px">
  <div class="division-head"><svg width="24" height="24" viewBox="0 0 24 24"><circle cx="12" cy="12" r="9" fill="none" stroke="#e2262c" stroke-width="3"/><circle cx="12" cy="12" r="4" fill="#e2262c"/></svg><h2>Digital<br>Technologies</h2></div>
  <p>Si vous voulez utiliser un passage du Lorem Ipsum, vous devez être sûr qu'il n'y a rien d'embarrassant caché dans le texte. Tous les générateurs</p>
  <span class="pill">More</span>
</div>
<div class="abs division" style="left:477px">
  <div class="division-head"><svg width="24" height="24" viewBox="0 0 24 24"><circle cx="12" cy="12" r="9" fill="none" stroke="#e2262c" stroke-width="3"/><circle cx="12" cy="12" r="4" fill="#e2262c"/></svg><h2>Digital File<br>Management</h2></div>
  <p>Si vous voulez utiliser un passage du Lorem Ipsum, vous devez être sûr qu'il n'y a rien d'embarrassant caché dans le texte. Tous les générateurs</p>
  <span class="pill">More</span>
</div>
<div class="abs division" style="left:672px">
  <div class="division-head"><svg width="24" height="24" viewBox="0 0 24 24"><circle cx="12" cy="12" r="9" fill="none" stroke="#e2262c" stroke-width="3"/><circle cx="12" cy="12" r="4" fill="#e2262c"/></svg><h2>Graphic imaging<br>services</h2></div>
  <p>Si vous voulez utiliser un passage du Lorem Ipsum, vous devez être sûr qu'il n'y a rien d'embarrassant caché dans le texte. Tous les générateurs</p>
  <span class="pill">More</span>
</div>

<div class="abs rule" style="top:610px"></div>

<div class="abs section-title" style="left:78px;top:628px">
  <svg width="22" height="20" viewBox="0 0 22 20"><rect x="1" y="1" width="20" height="18" fill="none" stroke="#e2262c" stroke-width="2"/><path d="M4 16 L9 9 L13 13 L16 10 L19 16Z" fill="#e2262c"/></svg>Our Portfolio
</div>

<div class="abs photo" style="left:78px;top:664px;width:180px;height:189px;background:linear-gradient(135deg,#f0f0f0 0%,#d9d9d9 40%,#e8a020 60%,#c0202a 80%,#f5d020 100%)" role="img" aria-label="Colour swatch fan and tape measure on architectural drawings"></div>
<div class="abs photo" style="left:274px;top:664px;width:179px;height:145px;background:linear-gradient(135deg,#3a7a20 0%,#e8d820 40%,#2840a0 65%,#e04070 100%)" role="img" aria-label="Loupe over a colourful printed calendar"></div>
<div class="abs photo" style="left:469px;top:664px;width:178px;height:189px;background:linear-gradient(160deg,#e0e0e0 0%,#c8c8c8 45%,#606060 60%,#d04050 85%,#eee 100%)" role="img" aria-label="Loupe resting on a printed brochure"></div>
<div class="abs photo" style="left:78px;top:869px;width:180px;height:141px;background:radial-gradient(circle at 60% 55%,#f0f0f0 0%,#e84a50 35%,#f0c020 55%,#40a0d0 70%,#e4e4e4 90%)" role="img" aria-label="Open colour swatch fan on white"></div>
<div class="abs photo" style="left:274px;top:826px;width:179px;height:184px;background:linear-gradient(170deg,#10183a 0%,#2a3a70 35%,#c02030 65%,#1a1010 100%)" role="img" aria-label="Large format printer output rollers"></div>
<div class="abs photo" style="left:469px;top:869px;width:178px;height:141px;background:radial-gradient(circle at 50% 50%,#3050c0 0%,#d03030 40%,#102070 75%,#050a30 100%)" role="img" aria-label="Abstract dimensional colour graphic"></div>

<div class="abs section-title" style="left:672px;top:628px">
  <svg width="20" height="20" viewBox="0 0 20 20"><rect x="1" y="2" width="18" height="17" fill="none" stroke="#e2262c" stroke-width="2"/><path d="M1 7 H19 M7 7 V19 M13 7 V19 M1 13 H19" stroke="#e2262c" stroke-width="1.5"/></svg>Latest News
</div>
<div class="abs news-item" style="top:661px"><div class="news-thumb" style="background:linear-gradient(135deg,#f0f0f0,#b8b8b8,#d05080)" role="img" aria-label="Stack of printed sheets"></div><div><div class="date">21st March, 2013</div><p>Contrairement à une opinion répandue, le Lorem Ipsum n'est pas.</p></div></div>
<div class="abs news-item" style="top:721px"><div class="news-thumb" style="background:linear-gradient(135deg,#eee,#c4c4c4,#888)" role="img" aria-label="Stack of newspapers"></div><div><div class="date">21st March, 2013</div><p>Contrairement à une opinion répandue, le Lorem Ipsum n'est pas.</p></div></div>
<div class="abs news-item" style="top:780px"><div class="news-thumb" style="background:linear-gradient(135deg,#4a8a30,#203a60,#8aa0c0)" role="img" aria-label="Printed leaf and city posters"></div><div><div class="date">21st March, 2013</div><p>Contrairement à une opinion répandue, le Lorem Ipsum n'est pas.</p></div></div>
<div class="abs link-red" style="left:672px;top:840px">Read More</div>

<div class="abs section-title" style="left:672px;top:869px">
  <svg width="20" height="20" viewBox="0 0 20 20"><rect x="1" y="2" width="18" height="17" fill="none" stroke="#e2262c" stroke-width="2"/><path d="M1 7 H19 M7 7 V19 M13 7 V19 M1 13 H19" stroke="#e2262c" stroke-width="1.5"/></svg>Testimonials
</div>
<div class="abs testimonial">
  Plusieurs variations de Lorem Ipsum peuvent être trouvées ici ou là, mais la majeure partie d'entre elles a été altérée par l'addition d'humour ou de mots aléatoires qui.ne resse mblent pas une seconde à.
  <div class="author">- Morten Ashby</div>
</div>
<div class="abs dots"><i></i><i></i><i></i></div>

<footer>
<div class="abs footer"></div>
<div class="abs footer-col" style="left:80px"><h3>About Us</h3><ul><li>Plusieurs</li><li>Variations de</li><li>Lorem Ipsum</li><li>Peuventêtre</li><li>Trouvées ici</li><li>Mais la majeure</li></ul></div>
<div class="abs footer-col" style="left:222px"><h3>Products &amp; Services</h3><ul><li>Plusieurs</li><li>Variations de</li><li>Lorem Ipsum</li><li>Peuventêtre</li></ul></div>
<div class="abs footer-col" style="left:390px"><h3>Color Graphics</h3><ul><li>Plusieurs</li><li>Variations de</li><li>Lorem Ipsum</li></ul></div>
<div class="abs footer-col" style="left:539px"><h3>Blog</h3><ul><li>Plusieurs</li><li>Variations de</li><li>Lorem Ipsum</li><li>Peuventêtre</li><li>Trouvées ici</li></ul></div>
<div class="abs footer-col" style="left:670px">
  <h3>Follow Us on</h3>
  <div class="social"><span>QN</span><span>Chirpa</span><span>Workrung</span></div>
  <h3 style="margin-top:12px">Newsletter Sign Up</h3>
  <div class="news-input"></div>
  <div class="btn-red submit">SUBMIT</div>
</div>
<div class="abs footer-base">Copyright 2013 Kelverton Imaging Inc. Harlow Office (555) 384-7290 Questions/Comments: email us at info@klmvxco.example</div>
</footer>
</body>
</html>
```